I need a business card to give to prospective clients. I am a freelance photographer who photographs most things (except weddings and social stuff) including nature, wildlife and interiors.
I want to look modern and stylish.
I am including a photograph although I am by no means certain that it should be used - what do you think?
More of my images can be seen and downloaded at my PixVault page - just search for Maren Tolbeck
Target Market(s)
Home owners selling or letting properties, private individuals wanting to buy prints
Industry/Entity Type
Business
Contact Information for Business Card
Maren Tolbeck Photography
Maren
Wrenfield Cottage, Mossbank Road, Pelsworth, Carrow Heath, KX41 2RB
Tel: +44 7000 418263. Email: maren@tolbeckstudio.example

```html
<!DOCTYPE html>
<html lang="en">
<head>
<meta charset="utf-8">
<title>Maren Tolbeck Photography – Business Card</title>
<link rel="stylesheet" href="https://fonts.googleapis.com/css2?family=Cinzel:wght@400&family=Montserrat:wght@400;600;700&display=swap">
<style>
  :root {
    --stage: #262626;
    --card-dark: #2b2829;
    --headline: #d9d9d9;
    --white: #ffffff;
    --accent-green: #1fa83a;
    --photo-light: #e2e2e2;
    --photo-mid: #9a9a9a;
    --photo-dark: #4a4a4a;
  }
  * { margin: 0; padding: 0; box-sizing: border-box; }
  html, body { width: 1200px; height: 900px; overflow: hidden; }
  body {
    background: var(--stage);
    display: flex;
    flex-direction: column;
    align-items: center;
    justify-content: center;
    gap: 48px;
  }
  .card {
    position: relative;
    width: 640px;
    height: 366px;
    overflow: hidden;
    box-shadow: 0 10px 30px rgba(0,0,0,0.45);
  }

  /* Front */
  .card-front {
    background: var(--card-dark);
    display: flex;
    align-items: center;
    justify-content: center;
  }
  .headline {
    font-family: "Cinzel", serif;
    font-weight: 400;
    color: var(--headline);
    font-size: 50px;
    line-height: 1.2;
    letter-spacing: 1px;
    text-align: left;
  }

  /* Back */
  .card-back { background: var(--photo-mid); }
  .photo-area {
    position: absolute;
    inset: 0;
    background: linear-gradient(180deg, var(--photo-light) 0%, #b8b8b8 50%, #858585 78%, var(--photo-dark) 100%);
  }
  .brand-name {
    position: absolute;
    left: 34px;
    top: 50px;
    font-family: "Montserrat", sans-serif;
    font-weight: 700;
    font-size: 29px;
    color: var(--white);
    letter-spacing: 0.5px;
    text-transform: uppercase;
    white-space: nowrap;
  }
  .services {
    position: absolute;
    left: 34px;
    bottom: 78px;
    display: flex;
    align-items: center;
    gap: 12px;
    font-family: "Montserrat", sans-serif;
    font-weight: 600;
    font-size: 24px;
    color: var(--white);
    text-transform: uppercase;
  }
  .services .divider {
    width: 3px;
    height: 26px;
    background: var(--accent-green);
  }
  .contact {
    position: absolute;
    left: 34px;
    right: 34px;
    bottom: 18px;
    display: flex;
    justify-content: space-between;
    font-family: "Montserrat", sans-serif;
    font-weight: 400;
    font-size: 14px;
    color: var(--white);
    white-space: nowrap;
  }
  .contact-item { display: flex; align-items: center; gap: 7px; }
  .contact-icon { width: 18px; height: 14px; }
</style>
</head>
<body>
  <section class="card card-front">
    <h1 class="headline">Looking for a<br>Photographer ?</h1>
  </section>

  <section class="card card-back">
    <div class="photo-area" role="img" aria-label="Black and white photograph of an elephant's legs and trunk against a pale sky"></div>

    <span class="brand-name">Maren Tolbeck Photography</span>

    <div class="services">
      <span>Nature</span><span class="divider"></span>
      <span>Wildlife</span><span class="divider"></span>
      <span>Interiors</span>
    </div>

    <div class="contact">
      <span class="contact-item">
        <svg class="contact-icon" viewBox="0 0 18 14" aria-hidden="true">
          <rect x="1" y="1" width="16" height="12" fill="none" stroke="var(--white)" stroke-width="1.4"/>
          <path d="M1 1 L9 8 L17 1" fill="none" stroke="var(--white)" stroke-width="1.4"/>
        </svg>
        maren@tolbeckstudio.example
      </span>
      <span class="contact-item">
        <svg class="contact-icon" viewBox="0 0 18 14" aria-hidden="true">
          <path d="M4 1 L7 1 L8 4 L6 5.5 C7 8 9 10 11.5 11 L13 9 L16 10 L16 13 C9 13 4 8 4 1 Z" fill="var(--white)"/>
        </svg>
        +44 7000 418263
      </span>
      <span class="contact-item">tolbeckstudio.example</span>
    </div>
  </section>
</body>
</html>
```